Cover for Lanterns Along the Quiet Shore of Being

Cover for a book that describes everything that happens to a person, from pre-birth life plans through growing in compassion and wisdom to death and living in the afterlife. The information is revealed in messages from people living in the life after this life. The title is Lessons Gathered From Every Season of Your Existence: Shared by Voices Dwelling Beyond the Veil. Author is T. Wesley Prandt. Book size is 6 by 9.

Target Market(s)

General

Font styles to use
Serif

```html
<!DOCTYPE html>
<html lang="en">
<head>
<meta charset="utf-8">
<title>Lanterns Along the Quiet Shore of Being — Book Cover</title>
<link rel="stylesheet" href="https://fonts.googleapis.com/css2?family=Merriweather:wght@700&family=Playfair+Display:ital,wght@1,400;1,600&family=Roboto+Slab:wght@300&display=swap">
<style>
  :root {
    --night: #0c1838;
    --deep-blue: #14245a;
    --aurora: #2f8f5a;
    --aurora-soft: #4fae72;
    --ink: #ffffff;
  }
  html, body {
    margin: 0;
    padding: 0;
    width: 800px;
    height: 1200px;
    overflow: hidden;
    background: var(--night);
  }
  .cover {
    position: relative;
    width: 800px;
    height: 1200px;
    overflow: hidden;
    color: var(--ink);
    text-align: center;
  }
  .cover-art {
    position: absolute;
    inset: 0;
    width: 800px;
    height: 1200px;
  }
  .tagline {
    position: absolute;
    top: 80px;
    left: 60px;
    right: 60px;
    margin: 0;
    font-family: "Playfair Display", serif;
    font-style: italic;
    font-weight: 400;
    font-size: 19px;
    line-height: 30px;
    letter-spacing: 0.3px;
  }
  .rule {
    position: absolute;
    left: 80px;
    width: 652px;
    height: 4px;
    background: var(--ink);
  }
  .rule-top { top: 241px; }
  .rule-bottom { top: 759px; }
  .title {
    position: absolute;
    top: 268px;
    left: 40px;
    right: 40px;
    margin: 0;
    font-family: "Merriweather", serif;
    font-weight: 700;
    font-size: 58px;
    line-height: 94px;
    letter-spacing: 1px;
    text-transform: uppercase;
  }
  .subtitle {
    position: absolute;
    top: 786px;
    left: 30px;
    right: 30px;
    margin: 0;
    font-family: "Roboto Slab", serif;
    font-weight: 300;
    font-size: 42px;
    line-height: 88px;
    letter-spacing: 0.5px;
  }
  .author {
    position: absolute;
    top: 1062px;
    left: 0;
    right: 0;
    margin: 0;
    font-family: "Playfair Display", serif;
    font-style: italic;
    font-weight: 600;
    font-size: 30px;
    letter-spacing: 1px;
  }
</style>
</head>
<body>
<main class="cover">
  <svg class="cover-art" role="img" aria-label="Night sky with green aurora ribbons sweeping across a deep blue starfield" viewBox="0 0 800 1200" preserveAspectRatio="none">
    <defs>
      <linearGradient id="sky" x1="0" y1="0" x2="0" y2="1">
        <stop offset="0" stop-color="#0f2046"/>
        <stop offset="0.5" stop-color="#132a55"/>
        <stop offset="1" stop-color="#0b1436"/>
      </linearGradient>
      <radialGradient id="glow-left" cx="0.05" cy="0.5" r="0.6">
        <stop offset="0" stop-color="#5fb07a" stop-opacity="0.9"/>
        <stop offset="1" stop-color="#2f8f5a" stop-opacity="0"/>
      </radialGradient>
      <radialGradient id="glow-top" cx="0.55" cy="0.12" r="0.55">
        <stop offset="0" stop-color="#3a9a62" stop-opacity="0.85"/>
        <stop offset="1" stop-color="#2f8f5a" stop-opacity="0"/>
      </radialGradient>
      <radialGradient id="glow-low" cx="0.75" cy="0.85" r="0.4">
        <stop offset="0" stop-color="#2f8f5a" stop-opacity="0.6"/>
        <stop offset="1" stop-color="#2f8f5a" stop-opacity="0"/>
      </radialGradient>
    </defs>
    <rect width="800" height="1200" fill="url(#sky)"/>
    <rect width="800" height="1200" fill="url(#glow-top)"/>
    <rect width="800" height="1200" fill="url(#glow-left)"/>
    <rect width="800" height="1200" fill="url(#glow-low)"/>
  </svg>

  <p class="tagline">A book that describes everything that happens to a person,<br>from pre-birth life plans through growing in compassion and<br>wisdom to death and living in the afterlife.</p>

  <div class="rule rule-top"></div>
  <h1 class="title">Lessons<br>Gathered From<br>Every Season<br>of Your<br>Existence</h1>
  <div class="rule rule-bottom"></div>

  <p class="subtitle">Shared by Voices Dwelling<br>Beyond the Veil</p>

  <p class="author">Written by T. Wesley Prandt</p>
</main>
</body>
</html>
```